SkyvornQ Business Cards and Stationary Design

Need a design for our business cards and stationary. I want to carry on the theme of the logo. I want the business cards to have a design on the back. I would like the business cards and the stationary to carry the same theme, design scheme, and branding

Target Market(s)

Airlines and Maintenance Facilities

Industry/Entity Type

Aviation

Contact Information for Business Card

Name
Position Title
Address: 4827 Trellis Hollow Road, Fort Pierce, Florida, 34951
Office Number
Mobile Number
Email
Website

Font styles to use
Serif
Sans Serif

Colors

Designer to choose colors to be used in the design.

```html
<!DOCTYPE html>
<html lang="en">
<head>
<meta charset="utf-8">
<title>SkyvornQ Business Card</title>
<link rel="stylesheet" href="https://fonts.googleapis.com/css2?family=Jost:wght@400;500;600&family=PT+Sans:wght@400&display=swap">
<style>
  :root{
    --navy:#10295e;
    --blue:#1f7fd0;
    --sky:#2f9be6;
    --ink:#2a2a2a;
    --grey:#555;
    --rule:#cfcfcf;
    --card:#ffffff;
    --stage:#e9ebee;
  }
  *{box-sizing:border-box;margin:0;padding:0}
  html,body{width:1200px;height:872px;overflow:hidden;background:var(--stage)}
  .canvas{position:relative;width:1200px;height:872px}
  .card{position:absolute;width:640px;height:366px;background:var(--card);
    box-shadow:0 6px 22px rgba(0,0,0,.18);overflow:hidden}
  .card--front{left:60px;top:60px}
  .card--back{left:500px;top:446px}

  .brand{display:flex;align-items:center;gap:16px}
  .brand__dot{width:78px;height:78px;border-radius:50%;background:var(--blue);flex:none}
  .brand__name{font-family:"Jost",sans-serif;font-weight:600;color:var(--navy);
    letter-spacing:6px;font-size:44px;line-height:1}

  .card--front .brand{position:absolute;left:120px;top:124px}
  .front__url{position:absolute;left:0;right:0;top:236px;text-align:center;
    font-family:"PT Sans",sans-serif;font-size:17px;letter-spacing:4px;color:var(--ink)}

  .card--back .brand{position:absolute;left:40px;top:120px;gap:12px}
  .card--back .brand__dot{width:56px;height:56px}
  .card--back .brand__name{font-size:32px;letter-spacing:4px}

  .back__rule{position:absolute;left:352px;top:40px;width:2px;height:200px;background:var(--rule)}
  .contact{position:absolute;left:376px;top:36px;font-family:"PT Sans",sans-serif;color:var(--ink)}
  .contact__name{font-family:"Jost",sans-serif;font-weight:600;font-size:23px;color:var(--navy);letter-spacing:.3px}
  .contact__role{font-family:"Jost",sans-serif;font-weight:400;font-size:19px;color:var(--grey);margin-bottom:12px}
  .contact__list{list-style:none;font-size:15px;line-height:22px}
  .contact__list li{display:flex;align-items:flex-start;gap:7px}
  .contact__list svg{width:14px;height:14px;margin-top:4px;flex:none}
  .contact__list .addr{margin-top:6px;line-height:19px}
  .contact__list .addr svg{margin-top:2px}

  .back__band{position:absolute;left:0;right:0;bottom:0;height:92px;
    background:linear-gradient(90deg,var(--navy) 0%,#1a4f9e 55%,var(--sky) 100%)}
</style>
</head>
<body>
<main class="canvas">

  <section class="card card--front" aria-label="Business card front">
    <div class="brand">
      <span class="brand__dot"></span>
      <span class="brand__name">SKYVORNQ</span>
    </div>
    <p class="front__url">www.skyvornq.com</p>
  </section>

  <section class="card card--back" aria-label="Business card back">
    <div class="brand">
      <span class="brand__dot"></span>
      <span class="brand__name">SKYVORNQ</span>
    </div>
    <div class="back__rule"></div>
    <div class="contact">
      <p class="contact__name">DARREN HOLLOWAY</p>
      <p class="contact__role">PRESIDENT</p>
      <ul class="contact__list">
        <li><svg viewBox="0 0 16 16"><circle cx="8" cy="8" r="7" fill="none" stroke="var(--navy)" stroke-width="1.5"/><path d="M5.5 4.5l1.5 1.5-1 1a5 5 0 0 0 3 3l1-1 1.5 1.5-1 1c-3 0-6-3-6-6z" fill="var(--navy)"/></svg>012-555-0148</li>
        <li><svg viewBox="0 0 16 16"><circle cx="8" cy="8" r="7" fill="none" stroke="var(--navy)" stroke-width="1.5"/><rect x="5.5" y="4" width="5" height="8" rx="1" fill="none" stroke="var(--navy)" stroke-width="1.3"/></svg>012-555-0149</li>
        <li><svg viewBox="0 0 16 16"><circle cx="8" cy="8" r="7" fill="none" stroke="var(--navy)" stroke-width="1.5"/><rect x="4" y="5.5" width="8" height="5.5" fill="none" stroke="var(--navy)" stroke-width="1.2"/><path d="M4 5.5l4 3 4-3" fill="none" stroke="var(--navy)" stroke-width="1.2"/></svg>info@skyvornq.com</li>
        <li><svg viewBox="0 0 16 16"><circle cx="8" cy="8" r="6.5" fill="none" stroke="var(--navy)" stroke-width="1.4"/><ellipse cx="8" cy="8" rx="2.8" ry="6.5" fill="none" stroke="var(--navy)" stroke-width="1.1"/><path d="M1.5 8h13M2.5 5h11M2.5 11h11" stroke="var(--navy)" stroke-width="1"/></svg>www.skyvornq.com</li>
        <li class="addr"><svg viewBox="0 0 16 16"><circle cx="8" cy="8" r="7" fill="none" stroke="var(--navy)" stroke-width="1.5"/><path d="M8 12.5s-3-3.2-3-5.3a3 3 0 0 1 6 0c0 2.1-3 5.3-3 5.3z" fill="var(--navy)"/><circle cx="8" cy="7.2" r="1" fill="#fff"/></svg><span>4827 Trellis Hollow Road,<br>Fort Pierce, Florida, 34951</span></li>
      </ul>
    </div>
    <div class="back__band" role="img" aria-label="Decorative blue swoosh band along the bottom edge"></div>
  </section>

</main>
</body>
</html>
```